Business Card for Multi-Brand Sportswear Company

We are looking for a business card which represents our company and the multiple brands within it.

The company: Fen Athletics (LTD)
The brands: Fen, TavaPuni, ElmStretch, Grit and Rain

Employees using these cards would be representing Fen Athletics, rather than any of the individual brands. You will see a current design within the uploaded files, to give some inspiration. The actual text of the brands is not necessary, but the logos should be on there is some format.

Our creative minds on this are stretched, so we are looking for someone to make this their own, and show us what a good business card should look like.

We may like to get these printed with spot gloss, so keep that in mind with your designs.

www.fenathletics.co.uk

Industry/Entity Type

Business

Contact Information for Business Card

Leo Pemberton-Hale
Operations Manager
(+44) 1632 960 418
Leo@fenathletics.co.uk
www.fenathletics.co.uk

Font styles to use
Sans Serif
Other font styles liked:
• Eurostile

Colors
ffffff

Requirements
Nice to have
• Dark (black) background

```html
<!DOCTYPE html>
<html lang="en">
<head>
<meta charset="utf-8">
<title>Fen Athletics – Business Card</title>
<link rel="stylesheet" href="https://fonts.googleapis.com/css2?family=Michroma&family=Open+Sans:wght@400;600&display=swap">
<style>
  :root {
    --page: #2b2522;
    --card: #141414;
    --panel: #d9d9d9;
    --panel-light: #e4e4e4;
    --rule: #1a1a1a;
    --ink-light: #d6d6d6;
    --ink-muted: #b5b5b5;
    --accent: #e0242b;
    --white: #ffffff;
    --badge-purple: #5c4a6b;
    --badge-grey: #9a9a9a;
    --badge-red: #d63a3a;
    --badge-dark: #333333;
  }
  * { box-sizing: border-box; margin: 0; padding: 0; }
  html, body { width: 1200px; height: 716px; overflow: hidden; }
  body {
    background: var(--page);
    display: flex;
    align-items: center;
    justify-content: center;
    gap: 50px;
    font-family: "Open Sans", sans-serif;
  }
  .card {
    position: relative;
    width: 540px;
    height: 309px;
    background: var(--card);
    overflow: hidden;
    box-shadow: 0 14px 30px rgba(0,0,0,.45);
  }
  .top-block {
    position: absolute;
    top: 0;
    background: var(--panel-light);
  }
  .top-block::after {
    content: "";
    position: absolute;
    left: -14px;
    right: 0;
    height: 3px;
    background: var(--rule);
  }
  .brand-panel {
    position: absolute;
    background: var(--panel);
    border-radius: 10px;
  }
  .brand-name {
    font-family: "Michroma", sans-serif;
    color: var(--rule);
    letter-spacing: 1px;
    text-align: right;
    white-space: nowrap;
  }
  .brand-badges { display: flex; }
  .badge {
    border-radius: 3px;
    border: 2px solid var(--badge-dark);
  }
  .badge--purple { background: var(--badge-purple); }
  .badge--grey { border-color: var(--badge-grey); }
  .badge--red { border-color: var(--badge-red); }
  .company {
    position: absolute;
    font-family: "Michroma", sans-serif;
    color: var(--ink-light);
    text-transform: uppercase;
    white-space: nowrap;
  }
  .edge-stripe {
    position: absolute;
    left: 0;
    right: 0;
    bottom: 20px;
    height: 10px;
    display: flex;
  }
  .edge-stripe .red { width: 40%; background: var(--accent); }
  .edge-stripe .white { flex: 1; background: var(--white); }

  /* front */
  .card--front .top-block { left: 248px; width: 250px; height: 194px; }
  .card--front .top-block::after { top: 54px; }
  .card--front .brand-panel { left: 173px; top: 80px; width: 325px; height: 114px; padding: 14px 16px 10px; }
  .card--front .brand-name { font-size: 20px; }
  .card--front .brand-badges { gap: 18px; margin-top: 16px; }
  .card--front .badge { width: 44px; height: 26px; }
  .card--front .company { left: 118px; top: 208px; font-size: 17px; letter-spacing: 4px; }

  /* back */
  .card--back .top-block { left: 205px; width: 165px; height: 118px; }
  .card--back .top-block::after { top: 36px; }
  .card--back .brand-panel { left: 130px; top: 50px; width: 240px; height: 68px; padding: 8px 12px; }
  .card--back .brand-name { font-size: 14px; }
  .card--back .brand-badges { gap: 12px; margin-top: 10px; }
  .card--back .badge { width: 30px; height: 18px; }
  .card--back .company { left: 100px; top: 128px; font-size: 12px; letter-spacing: 3px; }
  .person {
    position: absolute;
    left: 64px;
    top: 166px;
    color: var(--ink-light);
  }
  .person-name { font-size: 15px; font-weight: 600; }
  .person-role { font-size: 11px; color: var(--ink-muted); margin-left: 48px; }
  .contact {
    position: absolute;
    right: 30px;
    top: 160px;
    color: var(--ink-light);
    font-size: 11.5px;
    line-height: 1.45;
  }
  .contact .web { letter-spacing: 2px; margin-bottom: 8px; }
  .contact .address { margin-bottom: 6px; }
</style>
</head>
<body>
  <section class="card card--front" aria-label="Business card front">
    <div class="top-block"></div>
    <div class="brand-panel">
      <div class="brand-name">FEN ATHLETICS</div>
      <div class="brand-badges">
        <span class="badge badge--purple"></span>
        <span class="badge badge--grey"></span>
        <span class="badge badge--red"></span>
        <span class="badge"></span>
      </div>
    </div>
    <div class="company">Fen Athletics (LTD)</div>
    <div class="edge-stripe"><span class="red"></span><span class="white"></span></div>
  </section>

  <section class="card card--back" aria-label="Business card back">
    <div class="top-block"></div>
    <div class="brand-panel">
      <div class="brand-name">FEN ATHLETICS</div>
      <div class="brand-badges">
        <span class="badge badge--purple"></span>
        <span class="badge badge--grey"></span>
        <span class="badge badge--red"></span>
        <span class="badge"></span>
      </div>
    </div>
    <div class="company">Fen Athletics (LTD)</div>
    <div class="person">
      <div class="person-name">Leo Pemberton-Hale</div>
      <div class="person-role">Operations Manager</div>
    </div>
    <div class="contact">
      <div class="web">www.fenathletics.co.uk</div>
      <div class="address">Holme Yard, Carlton Fen,<br>Ely, CB7 4QT</div>
      <div>(+44) 1632 960 418</div>
      <div>Leo@fenathletics.co.uk</div>
    </div>
    <div class="edge-stripe"><span class="red"></span><span class="white"></span></div>
  </section>
</body>
</html>
```